"Outside the Box" Newsletter Design Project-Communications Company

I am looking for an Internal newsletter for a communications company that will be sent to our sales and leadership team.
This newsletter will deliver forecasting, sales results, stack rankings for the sales reps, total team results, corporate updates, success stories and updates from Training/Operations/Sales/Marketing (could be a box for each)I would also need a couple sections with a blank header and box to add info as needed, if something comes up that is not set in stone weekly.
I am looking for a template that looks sharp and professional that i can use every week by just dropping content in, (text and possibly an employee picture) I will need it in a format (possibly word) that the will keep the text in line when I drop it in each week. Once complete I can save to a pdf and would like to have the ability to drop it into the body of an email.

We have a racecar theme that we use when training our sales folks so we would like a little bit of that to the newsletter and also incorporate our color scheme from our company.

I would like four versions of the newsletter..all would match other than the title.
1. Week 1 title - Start your engines
2. Week 2 title - Looking for suggestions
3. Week 3 title - Looking for suggestions
4. Week 4 title - Approaching the finish line, this version would also include an employee spotlight, one seperate section.

If we could include a few pics around racing that would be good, not over the top, just a few to give it a little of that feel. Maybe a checkered flag with the QV logo on it, a racecar..anything else that may make sense.

I will attach our logo and our organization is called SMB (small/medium business) so that should also be placed on there somewhere. Final design would need to be two pages, sharp professional feel, my Vice President likes a very clean look, not too busy. I have also attached a sample newsletter from another group in our company, ours will not have as much content, we are much smaller but this is a sample (on a smaller scale)of what we are looking for. The company look and feel is what we want to follow. Thank you

Target Market(s)

Our Internal sales team.

Industry/Entity Type

Communications

Requirements
Must have
• Ability to update with my content without having things shift and fall out of line..format that will make that easy and then able to save to PDF..2 pages long.
Nice to have
• HTML template to match.

```html
<!DOCTYPE html>
<html lang="en">
<head>
<meta charset="utf-8">
<title>QV Weekly Recap – December 20, 2012</title>
<link href="https://fonts.googleapis.com/css2?family=Noto+Sans:wght@400;700&display=swap" rel="stylesheet">
<style>
  :root {
    --page-bg: #ebebeb;
    --card-bg: #ffffff;
    --ink: #2b2b2b;
    --body-ink: #3a3a3a;
    --brand: #6c2b90;
    --shadow: rgba(0, 0, 0, 0.12);
  }
  * { box-sizing: border-box; margin: 0; padding: 0; }
  html, body { width: 940px; height: 1200px; overflow: hidden; }
  body {
    position: relative;
    background: var(--page-bg);
    font-family: "Noto Sans", sans-serif;
    color: var(--body-ink);
  }
  .masthead { position: absolute; left: 29px; top: 18px; width: 880px; height: 78px; }
  .brand { position: absolute; left: 0; top: 0; display: flex; align-items: center; gap: 14px; height: 66px; }
  .flag { width: 58px; height: 50px; border-radius: 3px; background: linear-gradient(135deg, #3a3a3a, #9a9a9a); }
  .brand-name { font-size: 30px; font-weight: 700; color: var(--ink); line-height: 1; }
  .issue { position: absolute; right: 0; top: 14px; text-align: right; }
  .issue-date { font-size: 19px; font-weight: 700; color: var(--ink); }
  .issue-date span { font-weight: 400; }
  .issue-tagline { font-size: 13px; color: var(--ink); margin-top: 3px; }

  .card {
    position: absolute; background: var(--card-bg);
    box-shadow: 0 1px 3px var(--shadow); overflow: hidden;
  }
  .card-title { font-size: 18px; font-weight: 700; color: var(--ink); line-height: 1.2; }
  .card-text { font-size: 13px; line-height: 20.5px; color: var(--body-ink); }

  .vp-message { left: 29px; top: 105px; width: 880px; height: 147px; padding: 16px 29px 0 29px; }
  .vp-message .card-title { display: flex; align-items: center; gap: 8px; margin-bottom: 6px; }
  .vp-message .card-text { height: 102px; overflow: hidden; }

  .feature { left: 29px; top: 268px; width: 601px; height: 381px; }
  .feature-photo { height: 198px; background: linear-gradient(160deg, #8c8a86 0%, #5c5a58 45%, #2d2d2f 75%, #b9b6b0 100%); }
  .feature-body { padding: 12px 29px 0 29px; }
  .feature-body .card-title { margin-bottom: 6px; }

  .events { left: 646px; top: 268px; width: 263px; height: 381px; padding: 12px 14px; }
  .events .card-title { margin-bottom: 12px; }
  .event { margin-bottom: 19px; font-size: 13px; line-height: 20px; }
  .event-date { color: var(--brand); }
  .event-name { color: var(--ink); }

  .update { top: 666px; height: 240px; padding: 10px 29px 0 29px; }
  .update.ops { left: 29px; width: 426px; }
  .update.finance { left: 485px; width: 424px; }
  .accent { position: absolute; left: 0; top: 0; width: 7px; height: 40px; background: var(--brand); }
  .update .card-title { margin-bottom: 8px; }
  .update .card-text { height: 185px; overflow: hidden; }

  .spotlight { left: 29px; top: 924px; width: 880px; height: 252px; }
  .spotlight-body { position: absolute; left: 0; top: 0; width: 601px; height: 252px; padding: 8px 29px 0 29px; }
  .spotlight-body .card-title { font-size: 22px; margin-bottom: 6px; }
  .spotlight-body .card-text { height: 205px; overflow: hidden; }
  .spotlight-photo {
    position: absolute; left: 601px; top: 0; width: 279px; height: 252px;
    background: linear-gradient(135deg, #a89a86 0%, #6e6558 50%, #2e2a27 100%);
  }
</style>
</head>
<body>
  <header class="masthead">
    <div class="brand">
      <div class="flag" role="img" aria-label="Checkered racing flag"></div>
      <div class="brand-name">QV</div>
      <div class="flag" role="img" aria-label="Checkered racing flag"></div>
    </div>
    <div class="issue">
      <div class="issue-date">DECEMBER 20, 2012 <span>ISSUE</span></div>
      <div class="issue-tagline">A Weekly Recap of Important Things Going on QV That You Need To Know</div>
    </div>
  </header>

  <section class="card vp-message">
    <h2 class="card-title">
      <svg width="20" height="20" viewBox="0 0 20 20" aria-hidden="true">
        <circle cx="10" cy="6" r="4.5" fill="#e8b88a"/>
        <path d="M2 19 C2 13 6 11 10 11 C14 11 18 13 18 19 Z" fill="#4a90c9"/>
      </svg>
      Vice President Messages
    </h2>
    <p class="card-text">A wonderful serenity has taken possession of my entire soul, like these sweet mornings of spring which I enjoy with my whole heart. I am alone, and feel the charm of existence in this spot, which was created for the bliss of souls like mine. I am so happy, my dear friend, so absorbed in the exquisite sense of mere tranquil existence, that I neglect my talents. I should be incapable of drawing a single stroke at the present moment; and yet I feel that I never was a greater artist than now.</p>
  </section>

  <section class="card feature">
    <div class="feature-photo" role="img" aria-label="Race car crossing a checkered finish line on a track"></div>
    <div class="feature-body">
      <h2 class="card-title">WEEK 4 - Crossing the finish line in July</h2>
      <p class="card-text">Far far away, behind the word mountains, far from the countries Vokalia and Consonantia, there live the blind texts. Separated they live in Bookmarksgrove right at the coast of the Semantics, a large language ocean. A small river named Duden flows by their place and supplies it with the necessary regelialia. It is a paradisematic country, in which roasted parts of sentences fly into your mouth.</p>
    </div>
  </section>

  <aside class="card events">
    <h2 class="card-title">Upcoming Event</h2>
    <div class="event"><div class="event-date">Mon, July 23</div><div class="event-name">CR Q2 Presentation @3 pm</div></div>
    <div class="event"><div class="event-date">Fri, August 3</div><div class="event-name">Chicago Mid-Year Town Hall</div></div>
    <div class="event"><div class="event-date">June 1—August 31</div><div class="event-name">Double Down Challenge</div></div>
    <div class="event"><div class="event-date">June 1—August 31</div><div class="event-name">CR TooHot To Handle Contest</div></div>
  </aside>

  <section class="card update ops">
    <span class="accent"></span>
    <h2 class="card-title">Updates from Operations</h2>
    <p class="card-text">Far far away, behind the word mountains, far from the countries Vokalia and Consonantia, there live the blind texts. Separated they live in Bookmarksgrove right at the coast of the Semantics, a large language ocean. A small river named Duden flows by their place and supplies it with the necessary regelialia. It is a paradisematic country, in which roasted parts of sentences fly into your mouth. Even the all-powerful Pointing has no control about the blind texts it is an almost</p>
  </section>

  <section class="card update finance">
    <span class="accent"></span>
    <h2 class="card-title">Updates from Financial</h2>
    <p class="card-text">Far far away, behind the word mountains, far from the countries Vokalia and Consonantia, there live the blind texts. Separated they live in Bookmarksgrove right at the coast of the Semantics, a large language ocean. A small river named Duden flows by their place and supplies it with the necessary regelialia. It is a paradisematic country, in which roasted parts of sentences fly into your mouth. Even the all-powerful Pointing has no control about the blind texts it is an almost</p>
  </section>

  <section class="card spotlight">
    <div class="spotlight-body">
      <span class="accent"></span>
      <h2 class="card-title">Say Hello to Daniel Brooks from England.</h2>
      <p class="card-text">Lorem ipsum dolor sit amet, consectetuer adipiscing elit. Aenean commodo ligula eget dolor. Aenean massa. Cum sociis natoque penatibus et magnis dis parturient montes, nascetur ridiculus mus. Donec quam felis, ultricies nec, pellentesque eu, pretium quis, sem. Nulla consequat massa quis enim. Donec pede justo, fringilla vel, aliquet nec, vulputate eget, arcu. In enim justo, rhoncus ut, imperdiet a, venenatis vitae, justo. Nullam dictum felis eu pede mollis pretium. Integer tincidunt. Cras dapibus. Vivamus elementum semper nisi. Aenean vulputate eleifend tellus. Aenean leo ligula, porttitor eu, consequat vitae, eleifend ac, enim. Aliquam lorem ante, dapibus in, viverra quis, feugiat a, tellus. Phasellus viverra nulla ut</p>
    </div>
    <div class="spotlight-photo" role="img" aria-label="Portrait photo of the featured employee seated on a sofa"></div>
  </section>
</body>
</html>
```